Business card design for a dynamic IT consulting company

We need a business card design for a young firm, specialized in the Telecommunications/Consulting industry. The name of the company is Quindor and Partners Business Consulting Ltd. (Short name: Quindor and Partnes)
Quindor = solve read reverse, so we aim to be uncomplicated and solution-oriented. The small pipe in our logo is also related to the word solve. So we need a new business card design, which is simple, eye catching and something non traditional (I would probably prefer a square shaped design rather than a rectangle, but open for suggestions). Attached our logo.

Target Market(s)

Usually our customers are Tier1 Telecoms providers (Q-Netra, Palorix, etc) and their executives.

Industry/Entity Type

Business

Contact Information for Business Card

Name: Bence Tolnavari
Email: b.tolnavari@quindor.hu
Web: www.quindor.hu
Mobile: +36 30 518 2769
Title: Managing Director

Optional:
Company name: Quindor and Partners Ltd.
Address: 1087 Budapest, Tolvenka str. 28/C, Hungary

Font styles to use
Other font styles liked:
• helveticaneue_medium, Prime Regular are used now.

Colors

Designer to choose colors to be used in the design.

Requirements
Must have
• I would like to have a 2 sided design.
Nice to have
• I thought if we make the logo a bit bigger (without the company name), that could go to the back with the company name below. I though, if the pipe in the logo is somehow touchable on the business card, would be nice and unique.

```html
<!DOCTYPE html>
<html lang="en">
<head>
<meta charset="utf-8">
<title>Quindor and Partners – Business Card</title>
<link href="https://fonts.googleapis.com/css2?family=Work+Sans:wght@300;400;600;700&display=swap" rel="stylesheet">
<style>
  :root {
    --backdrop: #1b1b1b;
    --card-white: #ffffff;
    --card-grey-top: #676767;
    --card-grey-bottom: #4f4f4f;
    --accent-blue: #1e96d6;
    --accent-magenta: #b0277e;
    --text-dark: #4a4a4a;
    --text-light: #f2f2f2;
    --text-soft: #d6d6d6;
  }
  * { box-sizing: border-box; margin: 0; padding: 0; }
  html, body { width: 1200px; height: 963px; overflow: hidden; background: var(--backdrop); }
  body { font-family: "Work Sans", Arial, sans-serif; position: relative; }

  .card {
    position: absolute;
    left: 250px;
    width: 700px;
    height: 400px;
    border-radius: 18px;
    overflow: hidden;
    box-shadow: 0 18px 40px rgba(0,0,0,.55);
  }
  .card--front { top: 60px; background: var(--card-white); }
  .card--back {
    top: 503px;
    background: linear-gradient(160deg, var(--card-grey-top), var(--card-grey-bottom));
    display: flex; align-items: center; justify-content: center;
  }
  .card__art { position: absolute; inset: 0; }

  .holder { position: absolute; left: 48px; top: 26px; color: var(--text-light); }
  .holder__name { font-size: 25px; font-weight: 700; letter-spacing: .3px; }
  .holder__title { font-size: 15px; font-weight: 300; color: var(--text-soft); margin-top: 2px; }

  .company-mark {
    display: flex; align-items: center; gap: 12px;
    font-weight: 400; color: var(--text-dark);
  }
  .company-mark__square { width: 18px; height: 18px; background: var(--accent-blue); }
  .card--front .company-mark { position: absolute; left: 372px; top: 224px; font-size: 26px; }
  .card--back .company-mark { font-size: 42px; color: var(--text-light); gap: 18px; }
  .card--back .company-mark__square { width: 28px; height: 28px; background: var(--text-light); }

  .contacts { position: absolute; left: 48px; top: 196px; list-style: none; }
  .contacts li {
    display: flex; align-items: center; gap: 10px;
    font-size: 15px; color: var(--text-dark); font-weight: 400; line-height: 25px;
  }
  .contacts svg { width: 13px; height: 13px; flex: none; }

  .divider { position: absolute; left: 48px; right: 60px; top: 292px; height: 1px; background: var(--accent-blue); }

  .address {
    position: absolute; right: 60px; top: 312px; text-align: right;
    font-size: 15px; line-height: 24px; color: var(--text-dark);
  }
</style>
</head>
<body>

<section class="card card--front" aria-label="Business card front">
  <svg class="card__art" viewBox="0 0 700 400" preserveAspectRatio="none">
    <defs>
      <linearGradient id="greyFill" x1="0" y1="0" x2="1" y2="1">
        <stop offset="0" stop-color="#6a6a6a"/>
        <stop offset="1" stop-color="#4d4d4d"/>
      </linearGradient>
    </defs>
    <path d="M0,0 H700 V250 C610,180 470,178 340,142 C210,104 90,66 0,88 Z" fill="url(#greyFill)"/>
    <path d="M0,88 C90,66 210,104 340,142 C470,178 610,180 700,250" fill="none" stroke="var(--accent-blue)" stroke-width="9"/>
  </svg>

  <div class="holder">
    <div class="holder__name">Bence Tolnavari</div>
    <div class="holder__title">Managing Director</div>
  </div>

  <div class="company-mark">
    <span class="company-mark__square"></span>
    <span class="company-mark__name">Quindor &amp; Partners</span>
  </div>

  <ul class="contacts">
    <li>
      <svg viewBox="0 0 16 16"><path d="M4 1 L6.5 4 L5 6 C6 8.5 7.5 10 10 11 L12 9.5 L15 12 L13 15 C7 14.5 1.5 9 1 3 Z" fill="var(--accent-blue)"/></svg>
      +36 30 518 2769
    </li>
    <li>
      <svg viewBox="0 0 16 16"><rect x="1" y="3" width="14" height="10" fill="none" stroke="var(--accent-blue)" stroke-width="1.6"/><path d="M1 3 L8 9 L15 3" fill="none" stroke="var(--accent-blue)" stroke-width="1.6"/></svg>
      b.tolnavari@quindor.hu
    </li>
    <li>
      <svg viewBox="0 0 16 16"><circle cx="8" cy="8" r="6.5" fill="none" stroke="var(--accent-blue)" stroke-width="1.5"/><path d="M1.5 8 H14.5 M8 1.5 C5 5 5 11 8 14.5 C11 11 11 5 8 1.5" fill="none" stroke="var(--accent-blue)" stroke-width="1.2"/></svg>
      www.quindor.hu
    </li>
  </ul>

  <div class="divider"></div>

  <address class="address" style="font-style:normal">
    1087 Budapest,<br>
    Tolvenka str. 28/C, Hungary
  </address>
</section>

<section class="card card--back" aria-label="Business card back">
  <div class="company-mark">
    <span class="company-mark__square"></span>
    <span class="company-mark__name">Quindor &amp; Partners</span>
  </div>
</section>

</body>
</html>
```